Velmora Freightway Solutions Business cards

Would like a very unique design catchy but professional for business cards. Please use log provided.Marlon WellsCeo and Founder TransCon Logistix Solutions1-888-913-3225mwells@tlsolutionsus.comwww.tlsolutionsus.com

```html
<!DOCTYPE html>
<html lang="en">
<head>
<meta charset="utf-8">
<title>Velmora Freightway Solutions — Business Cards</title>
<link rel="stylesheet" href="https://fonts.googleapis.com/css2?family=Montserrat:wght@600;700&display=swap">
<style>
  :root {
    --backdrop: #ece9e4;
    --card-blue: #1375bc;
    --card-white: #ffffff;
    --ink-white: #ffffff;
    --brand-blue: #1565b0;
    --card-shadow: rgba(0, 0, 0, 0.35);
  }
  * { margin: 0; padding: 0; box-sizing: border-box; }
  html, body {
    width: 1200px;
    height: 900px;
    overflow: hidden;
    background: var(--backdrop);
    font-family: "Montserrat", sans-serif;
  }
  .canvas {
    position: relative;
    width: 1200px;
    height: 900px;
  }
  .card {
    position: absolute;
    left: 330px;
    box-shadow: 2px 3px 6px var(--card-shadow);
  }
  .card-front {
    top: 90px;
    width: 555px;
    height: 343px;
    background: var(--card-blue);
    color: var(--ink-white);
    text-align: center;
  }
  .card-back {
    top: 469px;
    width: 559px;
    height: 343px;
    background: var(--card-white);
  }
  .holder-name {
    position: absolute;
    top: 97px;
    left: 0;
    right: 0;
    font-size: 19px;
    font-weight: 700;
    letter-spacing: 0.5px;
  }
  .holder-title {
    position: absolute;
    top: 119px;
    left: 0;
    right: 0;
    font-size: 15px;
    font-weight: 600;
  }
  .contact-divider {
    position: absolute;
    top: 158px;
    left: 187px;
    width: 180px;
    height: 24px;
  }
  .contact-list {
    position: absolute;
    top: 186px;
    left: 0;
    right: 0;
    list-style: none;
    font-weight: 700;
  }
  .contact-phone { font-size: 17px; line-height: 21px; letter-spacing: 0.3px; }
  .contact-email, .contact-web { font-size: 15px; line-height: 20px; letter-spacing: 0.2px; }
  .brand-lockup {
    position: absolute;
    top: 150px;
    left: 0;
    right: 0;
    display: flex;
    justify-content: center;
    align-items: center;
    gap: 12px;
  }
  .brand-mark {
    width: 22px;
    height: 22px;
    background: var(--brand-blue);
  }
  .brand-name {
    font-size: 24px;
    font-weight: 700;
    color: var(--brand-blue);
    letter-spacing: 0.3px;
  }
</style>
</head>
<body>
<main class="canvas">
  <section class="card card-front">
    <h1 class="holder-name">CALDER VOSS</h1>
    <p class="holder-title">CEO and Founder</p>
    <svg class="contact-divider" viewBox="0 0 180 24" aria-hidden="true">
      <g stroke="#ffffff" stroke-width="1">
        <line x1="0" y1="12" x2="51" y2="12"/>
        <line x1="129" y1="12" x2="180" y2="12"/>
      </g>
      <g fill="#ffffff">
        <circle cx="63" cy="12" r="11"/>
        <circle cx="89" cy="12" r="11"/>
        <circle cx="115" cy="12" r="11"/>
      </g>
      <g fill="#1375bc">
        <path d="M57 9 q6 -4 12 0 v2 h-3 v-1 h-6 v1 h-3z"/>
        <rect x="58" y="12" width="10" height="5" rx="1"/>
        <rect x="83" y="8" width="12" height="8"/>
      </g>
      <path d="M83 8 l6 5 l6 -5" fill="none" stroke="#ffffff" stroke-width="1"/>
      <circle cx="115" cy="12" r="6" fill="#1375bc"/>
      <path d="M111 10 q3 -2 5 1 q2 2 3 0 M112 15 q2 -2 4 0" fill="none" stroke="#ffffff" stroke-width="1.2"/>
    </svg>
    <ul class="contact-list">
      <li class="contact-phone">1-888-470-6158</li>
      <li class="contact-email">dpike@vfwayroutes.com</li>
      <li class="contact-web">www.vfwayroutes.com</li>
    </ul>
  </section>

  <section class="card card-back">
    <div class="brand-lockup">
      <span class="brand-mark" aria-hidden="true"></span>
      <span class="brand-name">Velmora Freightway Solutions</span>
    </div>
  </section>
</main>
</body>
</html>
```